Brell Stone Company Business Cards

Front and Back Business Card - logo and text setup - cool design. I need workable photoshop or illustrator files so I can setup each employee card with design that is created
Updates

Hi everyone, thank you for the great entries. Please no more white and blue cards - there are so many already - black and silver only now please. thanks!

Target Market(s)

Construction Industry - Facility Managers

Industry/Entity Type

Construction

Contact Information for Business Card

I really like contemporary simplistic looks - clean neat....not opposed to seeing some black backrounds

Requirements
Must have
• Logo/website address with design on front only - www.brellstone-example.com (logo attached)
• Back:
• Name/Title/Company Address/Phone/email address
Nice to have
• Cool design
Should not have
• Nothing gimmicky like Fire or Water - since we are a Fire Protection company - it has all been done

```html
<!DOCTYPE html>
<html lang="en">
<head>
<meta charset="utf-8">
<title>Brell Stone Company Business Cards</title>
<link href="https://fonts.googleapis.com/css2?family=Lato:wght@400;700;900&display=swap" rel="stylesheet">
<style>
  :root {
    --backdrop: #5b5b5b;
    --jet: #151617;
    --graphite: #2b2d30;
    --silver: #b8bcc2;
    --silver-light: #dfe2e6;
    --silver-dark: #7c8188;
    --paper: #eef0f2;
    --ink: #3a3c40;
  }
  html, body {
    margin: 0;
    padding: 0;
    width: 1200px;
    height: 802px;
    overflow: hidden;
    background: var(--backdrop);
    font-family: "Lato", Arial, sans-serif;
  }
  .canvas {
    position: relative;
    width: 1200px;
    height: 802px;
  }
  .card {
    position: absolute;
    top: 274px;
    width: 442px;
    height: 264px;
    box-shadow: 2px 3px 6px rgba(0,0,0,0.45);
    overflow: hidden;
  }
  .card-front { left: 136px; background: var(--paper); }
  .card-back { left: 624px; background: var(--jet); }

  .side-band {
    position: absolute;
    left: 0; top: 0;
    width: 50px; height: 100%;
    background: var(--jet);
  }
  .side-dashes {
    position: absolute;
    left: 50px; top: 0;
    width: 6px; height: 264px;
  }
  .wordmark {
    position: absolute;
    font-weight: 900;
    letter-spacing: -0.5px;
    white-space: nowrap;
    line-height: 1;
  }
  .card-front .wordmark {
    right: 34px;
    top: 46px;
    font-size: 32px;
    color: var(--jet);
  }
  .card-back .wordmark {
    left: 0; right: 0;
    top: 100px;
    text-align: center;
    font-size: 46px;
    color: var(--silver);
  }
  .contact {
    position: absolute;
    left: 82px;
    top: 130px;
    color: var(--ink);
  }
  .person-name {
    margin: 0;
    font-size: 16.5px;
    font-weight: 700;
    color: var(--jet);
    letter-spacing: -0.2px;
    line-height: 1.1;
  }
  .person-name .surname { color: var(--silver-dark); }
  .person-title {
    margin: 1px 0 6px;
    font-size: 13px;
    line-height: 1.2;
  }
  .contact-line {
    display: flex;
    align-items: center;
    gap: 4px;
    font-size: 12.5px;
    line-height: 1.25;
    margin: 0 0 2px;
  }
  .contact-line svg { width: 10px; height: 10px; fill: var(--jet); }
  .address {
    margin: 6px 0 0 2px;
    font-size: 12.5px;
    line-height: 1.25;
  }
  .website {
    position: absolute;
    left: 0; right: 0;
    top: 214px;
    text-align: center;
    color: var(--silver-light);
    font-size: 14px;
  }
</style>
</head>
<body>
<main class="canvas">
  <section class="card card-front" aria-label="Card front">
    <div class="side-band"></div>
    <svg class="side-dashes" width="6" height="264" viewBox="0 0 6 264" aria-hidden="true">
      <defs>
        <linearGradient id="dashFade" gradientUnits="userSpaceOnUse" x1="0" y1="0" x2="0" y2="264">
          <stop offset="0" stop-color="#7c8188"/>
          <stop offset="1" stop-color="#dfe2e6"/>
        </linearGradient>
      </defs>
      <line x1="3" y1="0" x2="3" y2="264" stroke="url(#dashFade)" stroke-width="6" stroke-dasharray="12 3"/>
    </svg>
    <div class="wordmark">Brell Stone</div>
    <div class="contact">
      <p class="person-name">MARCUS <span class="surname">HALE</span></p>
      <p class="person-title">Managing Director</p>
      <p class="contact-line">
        <svg viewBox="0 0 10 10" aria-hidden="true"><path d="M1 4 Q5 0 9 4 L8 5 L6.5 4 L6.5 3.2 Q5 2.7 3.5 3.2 L3.5 4 L2 5 Z M2.5 5.5 L7.5 5.5 L8.5 9 L1.5 9 Z"/></svg>
        044-555 010 234
      </p>
      <p class="contact-line">
        <svg viewBox="0 0 10 10" aria-hidden="true"><path d="M0.5 2 H9.5 V8 H0.5 Z M1.2 2.6 L5 5.6 L8.8 2.6" stroke="#eef0f2" stroke-width="0.8"/></svg>
        info@brellstone-example.com
      </p>
      <p class="address">421, Address line here,<br>45452,Country Name</p>
    </div>
  </section>

  <section class="card card-back" aria-label="Card back">
    <div class="wordmark">Brell Stone</div>
    <div class="website">www.brellstone-example.com</div>
  </section>
</main>
</body>
</html>
```